Social Media Cover and Profile

We already have our own logo. We just need a fresh design on our social media pages. We are not happy with our current designs. We would like to incorporate our ZING billboard and the colors are blue (#05143f) and white. You can also incorporate silver as well. We are a family law office (Divorce and Custody) We no longer want to incorporate the Capital of Harrisburg photo that we are currently using. You can look at our Facebook page; The Law Office of Milo T. Brennick.

Target Market(s)

Potential Clients

Industry/Entity Type

Family Law

Logo Text

Our Logo Is The Law Office of Milo T. Brennick with the Sheild

Requirements
Must have
• Text to include:
Central Pennslyvania's Premier Family Law Firm

Ability to be resized to and used as all images in social media, including but not limited to: Youtube Channel art, Facebook Cover and Profile.
Nice to have
• Darker color but we are open to "bright" ideas.

```html
<!DOCTYPE html>
<html lang="en">
<head>
<meta charset="utf-8">
<title>ZING – Social Media Cover</title>
<link rel="stylesheet" href="https://fonts.googleapis.com/css2?family=Noto+Serif:wght@600&display=swap">
<style>
  :root {
    --navy: #05143f;
    --navy-deep: #020d33;
    --silver: #96979a;
    --silver-light: #c9cacd;
    --paper: #f2f2f2;
    --panel-top: #f6f6f7;
    --panel-bottom: #d9dadd;
    --ink: #0b1845;
  }
  * { margin: 0; padding: 0; box-sizing: border-box; }
  html, body {
    width: 1200px;
    height: 720px;
    overflow: hidden;
    background: var(--paper);
  }
  .canvas {
    position: relative;
    width: 1200px;
    height: 720px;
    background: var(--paper);
  }
  .cover-banner {
    position: absolute;
    left: 51px;
    top: 154px;
    width: 1101px;
    height: 420px;
    background: linear-gradient(to bottom, #e4e5e7 0%, var(--panel-top) 18%, #f3f3f4 60%, var(--panel-bottom) 100%);
    box-shadow: 0 6px 10px rgba(0, 0, 0, 0.35);
    overflow: hidden;
  }
  .cover-banner__waves {
    position: absolute;
    inset: 0;
    width: 100%;
    height: 100%;
  }
  .cover-banner__wordmark {
    position: absolute;
    left: 0;
    right: 0;
    top: 70px;
    text-align: center;
    font-family: "Noto Serif", Georgia, serif;
    font-weight: 600;
    font-size: 236px;
    line-height: 1;
    letter-spacing: 24px;
    padding-left: 24px;
    color: var(--silver);
  }
  .cover-banner__tagline {
    position: absolute;
    left: 0;
    right: 0;
    top: 309px;
    text-align: center;
    font-family: "Noto Serif", Georgia, serif;
    font-weight: 600;
    font-size: 28.5px;
    line-height: 1;
    color: var(--ink);
  }
</style>
</head>
<body>
  <main class="canvas">
    <section class="cover-banner">
      <svg class="cover-banner__waves" viewBox="0 0 1835 700" preserveAspectRatio="none" aria-hidden="true">
        <defs>
          <linearGradient id="navyFade" x1="0" y1="0" x2="0" y2="1">
            <stop offset="0" stop-color="#020d33"/>
            <stop offset="1" stop-color="#05143f"/>
          </linearGradient>
        </defs>
        <path class="wave wave--left" fill="url(#navyFade)"
          d="M0 0 H205 C150 40 80 70 30 95 C110 150 135 230 120 300 C100 380 70 430 90 490 C120 580 200 620 232 700 H0 Z"/>
        <path fill="none" stroke="#c9cacd" stroke-width="3"
          d="M180 0 C130 40 60 70 0 85"/>
        <path fill="none" stroke="#c9cacd" stroke-width="3"
          d="M20 105 C85 160 105 235 95 300 C80 380 50 430 68 495 C95 580 175 620 210 700"/>
        <path class="wave wave--right" fill="url(#navyFade)"
          d="M1835 0 H1630 C1690 45 1760 70 1810 92 C1745 140 1710 210 1715 280 C1722 360 1770 420 1760 480 C1745 570 1640 620 1603 700 H1835 Z"/>
        <path fill="none" stroke="#c9cacd" stroke-width="3"
          d="M1655 0 C1710 45 1775 70 1835 80"/>
        <path fill="none" stroke="#c9cacd" stroke-width="3"
          d="M1815 105 C1760 150 1735 215 1740 280 C1748 360 1795 420 1785 485 C1770 570 1670 620 1630 700"/>
      </svg>
      <h1 class="cover-banner__wordmark">ZING</h1>
      <p class="cover-banner__tagline">Central Pennslyvania's Premier Family Law Firm</p>
    </section>
  </main>
</body>
</html>
```